Cat-products company needs smart, yet endearing, business card

We need a business card design for a new, but up-and-running, business based in Honolulu, Hawaii. The business is Purrnest Nook Co. Our first product is the most environmentally-friendly cat grass kit ever seen on the planet. Future products, currently in the R&D phase, will include a variety of exciting cat scratchers. We also do consulting work to help apartment-dwellers make their home more cat-friendly and, in the future, plan on doing full, custom installs of structure to create high walkways for cats.

Target Market(s)

Middle-aged, apartment-dwelling, middle-class workers who own 1 or more cats and who dote on them.

Industry/Entity Type

Pet Care

Contact Information for Business Card

A striking, professional, yet warm and friendly design is what we're after.

Font styles to use
Serif
Sans Serif
Other font styles liked:
• Comfortaa

Colors

Designer to choose colors to be used in the design.

Requirements
Must have
• The company logo: (see attachment)
• The company name: Purrnest Nook Co
• The web address: www.purrnestnookco.com
• Email: support@purrnestnookco.com
• Phone: +1 (808) 571 6023
• Update (Fri Jun 30 3017 7:45pm Hawaii Time) I would like, is possible, uploaded picture of the cat grass kit on the back of the card with some text along the lines of: Purrnest Nook Co - Maker Of The Leafiest Feline Sprout Set Yet
Nice to have
• A cat picture, cartoon, real or silhouette that illustrates cats in action and/or relaxing; ie using the apartment space to live, play and relax in and being well-contented.
• Most of the website is done in the font: Comfortaa. It might be nice to continue using this for brand consistency.
Should not have
• Hard-to-read fonts.

```html
<!DOCTYPE html>
<html lang="en">
<head>
<meta charset="utf-8">
<title>Purrnest Nook Co — Round Business Card</title>
<link rel="stylesheet" href="https://fonts.googleapis.com/css2?family=Fredoka:wght@600&family=Source+Sans+3:wght@400;600&display=swap">
<style>
  :root {
    --backdrop: #262626;
    --card-light: #e8e8e8;
    --card-dark: #5a352f;
    --brand-brown: #5b3a33;
    --brand-gold: #f6b100;
    --ink-light: #ffffff;
    --ink-soft: #f1e7e4;
  }
  * { margin: 0; padding: 0; box-sizing: border-box; }
  html, body {
    width: 1200px; height: 900px; overflow: hidden;
    background: var(--backdrop);
  }
  .canvas { position: relative; width: 1200px; height: 900px; }
  .card {
    position: absolute; top: 215px;
    width: 414px; height: 414px; border-radius: 50%;
    box-shadow: 0 3px 8px rgba(0,0,0,0.45);
  }
  .card--front {
    left: 164px; background: var(--card-light);
    display: flex; flex-direction: column; align-items: center; justify-content: center;
  }
  .brand-mark {
    width: 96px; height: 96px; border-radius: 10px;
    background: var(--brand-brown); margin-bottom: 22px;
  }
  .brand-name {
    font-family: "Fredoka", sans-serif; font-weight: 600;
    font-size: 40px; line-height: 1.05; color: var(--brand-brown);
    text-align: center;
  }
  .card--back {
    left: 623px; background: var(--card-dark);
    font-family: "Source Sans 3", sans-serif; color: var(--ink-light);
    text-align: center;
  }
  .person-name {
    position: absolute; top: 88px; width: 100%;
    font-weight: 600; font-size: 20px; letter-spacing: 0.3px;
  }
  .person-role {
    position: absolute; top: 117px; width: 100%;
    font-size: 18px; color: var(--ink-soft);
  }
  .contact-list {
    position: absolute; top: 243px; width: 100%; list-style: none;
    font-size: 18px; line-height: 28px;
  }
  .contact-item { display: flex; align-items: center; justify-content: center; gap: 6px; }
  .contact-icon { width: 14px; height: 14px; fill: var(--ink-light); }
</style>
</head>
<body>
<main class="canvas">
  <section class="card card--front">
    <div class="brand-mark"></div>
    <p class="brand-name">Purrnest<br>Nook Co</p>
  </section>

  <section class="card card--back">
    <h1 class="person-name">MARLOW KEANE</h1>
    <p class="person-role">Managing Director</p>
    <ul class="contact-list">
      <li class="contact-item">
        <svg class="contact-icon" viewBox="0 0 24 24"><path d="M6.6 10.8a15.1 15.1 0 0 0 6.6 6.6l2.2-2.2c.3-.3.7-.4 1-.2 1.1.4 2.3.6 3.6.6.6 0 1 .4 1 1V20c0 .6-.4 1-1 1A17 17 0 0 1 3 4c0-.6.4-1 1-1h3.5c.6 0 1 .4 1 1 0 1.3.2 2.5.6 3.6.1.3 0 .7-.2 1z"/></svg>
        <span>+1 (808) 571 6023</span>
      </li>
      <li class="contact-item">
        <svg class="contact-icon" viewBox="0 0 24 24"><path d="M2 5h20v14H2z M2 5l10 8 10-8" stroke="#5a352f" stroke-width="1.6"/></svg>
        <span>support@purrnestnookco.com</span>
      </li>
      <li class="contact-item">
        <svg class="contact-icon" viewBox="0 0 24 24"><circle cx="12" cy="12" r="10"/><path d="M7 8c2 0 3 1 3 3s2 2 2 4-1 3-1 4M15 5c0 2 1 3 3 3s2 2 2 3" stroke="#5a352f" stroke-width="1.6" fill="none"/></svg>
        <span>www.purrnestnookco.com</span>
      </li>
    </ul>
  </section>
</main>
</body>
</html>
```